Velmora Freightway Solutions Business cards

Would like a very unique design catchy but professional for business cards. Please use log provided.Marlon WellsCeo and Founder TransCon Logistix Solutions1-888-913-3225mwells@tlsolutionsus.comwww.tlsolutionsus.com

```html
<!DOCTYPE html>
<html lang="en">
<head>
<meta charset="utf-8">
<title>Velmora Freightway Solutions – Business Cards</title>
<link rel="stylesheet" href="https://fonts.googleapis.com/css2?family=Lato:wght@400;700;900&display=swap">
<style>
  :root {
    --brand-blue: #1373bd;
    --brand-navy: #0f2a4a;
    --brand-red: #e8202a;
    --ink: #1d1d1f;
    --paper: #ffffff;
    --backdrop: #e6e6e3;
    --rule: #9a9a9a;
  }
  * { margin: 0; padding: 0; box-sizing: border-box; }
  html, body {
    width: 1200px; height: 960px; overflow: hidden;
    background: var(--backdrop);
    font-family: "Lato", sans-serif;
    color: var(--ink);
  }
  .stage { position: relative; width: 1200px; height: 960px; }

  .card {
    position: absolute;
    background: var(--paper);
    border-radius: 28px;
    overflow: hidden;
    box-shadow: 0 6px 18px rgba(0,0,0,0.18);
  }

  /* Front */
  .card-front { left: 237px; top: 47px; width: 720px; height: 406px; }
  .front-brand {
    position: absolute; left: 0; right: 0; top: 130px;
    display: flex; align-items: center; justify-content: center; gap: 22px;
  }
  .brand-square { width: 44px; height: 44px; background: var(--brand-red); flex: none; }
  .front-name {
    color: var(--brand-blue); font-weight: 900;
    font-size: 50px; line-height: 1.05; letter-spacing: 0.5px;
    text-transform: uppercase;
  }
  .front-web {
    position: absolute; left: 0; right: 0; top: 358px;
    display: flex; align-items: center; justify-content: center; gap: 12px;
  }
  .front-web .line { width: 90px; height: 2px; background: var(--brand-blue); }
  .front-web .url { font-size: 17px; letter-spacing: 2.5px; color: #333; }

  /* Back */
  .card-back { left: 252px; top: 509px; width: 705px; height: 406px; }
  .back-band { position: absolute; left: 0; top: 0; }
  .holder { position: absolute; right: 32px; top: 22px; text-align: right; color: #fff; }
  .holder-name { font-weight: 700; font-size: 23px; letter-spacing: 0.3px; }
  .holder-title { font-size: 17px; margin-top: 6px; letter-spacing: 0.4px; }

  .back-brand { position: absolute; left: 40px; top: 172px; }
  .back-name {
    color: var(--brand-blue); font-weight: 700; font-size: 25px;
    line-height: 1.15; letter-spacing: 0.6px; text-transform: uppercase;
  }
  .back-rule { margin-top: 8px; width: 350px; height: 2px; background: var(--brand-red); }

  .contact { position: absolute; left: 40px; top: 294px; list-style: none; }
  .contact li { display: flex; align-items: center; gap: 10px; font-size: 17px; height: 30px; }
  .contact svg { width: 15px; height: 15px; fill: var(--brand-blue); flex: none; }
  .divider { position: absolute; left: 305px; top: 328px; width: 1px; height: 46px; background: var(--rule); }
  .address { position: absolute; left: 325px; top: 326px; font-size: 17px; line-height: 27px; font-style: normal; }
</style>
</head>
<body>
<main class="stage">

  <section class="card card-front" aria-label="Card front">
    <div class="front-brand">
      <span class="brand-square"></span>
      <span class="front-name">Velmora Freightway<br>Solutions</span>
    </div>
    <div class="front-web">
      <span class="line"></span>
      <span class="url">www.vfwayroutes.com</span>
      <span class="line"></span>
    </div>
  </section>

  <section class="card card-back" aria-label="Card back">
    <svg class="back-band" width="705" height="406" viewBox="0 0 705 406">
      <path d="M0,0 H705 V210 C580,130 430,72 260,66 C150,62 60,74 0,92 Z" fill="var(--brand-navy)"/>
      <path d="M0,0 H705 V180 C570,100 420,52 250,50 C140,49 55,60 0,76 Z" fill="var(--brand-blue)"/>
      <path d="M0,82 C70,70 150,66 260,66" stroke="#fff" stroke-width="3" fill="none"/>
    </svg>

    <div class="holder">
      <div class="holder-name">DORIAN PIKE</div>
      <div class="holder-title">CEO AND FOUNDER</div>
    </div>

    <div class="back-brand">
      <div class="back-name">Velmora Freightway<br>Solutions</div>
      <div class="back-rule"></div>
    </div>

    <ul class="contact">
      <li>
        <svg viewBox="0 0 24 24"><path d="M6.6 10.8a15.1 15.1 0 0 0 6.6 6.6l2.2-2.2a1 1 0 0 1 1-.25 11.4 11.4 0 0 0 3.6.57 1 1 0 0 1 1 1V20a1 1 0 0 1-1 1A17 17 0 0 1 3 4a1 1 0 0 1 1-1h3.5a1 1 0 0 1 1 1c0 1.25.2 2.45.57 3.57a1 1 0 0 1-.25 1z"/></svg>
        1-888-470-6158
      </li>
      <li>
        <svg viewBox="0 0 24 24"><path d="M2 5h20v14H2z M4 7v.5l8 5 8-5V7z" fill-rule="evenodd"/></svg>
        dpike@vfwayroutes.com
      </li>
      <li>
        <svg viewBox="0 0 24 24"><path d="M12 2a10 10 0 1 0 0 20 10 10 0 0 0 0-20zm0 2c.9 1.2 1.6 2.6 2 4h-4c.4-1.4 1.1-2.8 2-4zM4.3 14a8 8 0 0 1 0-4h3.4a16 16 0 0 0 0 4zm.8 2h3c.3 1.3.8 2.5 1.4 3.6A8 8 0 0 1 5.1 16zM8 8H5.1a8 8 0 0 1 4.4-3.6C8.9 5.5 8.4 6.7 8 8zm4 12c-.9-1.2-1.6-2.6-2-4h4c-.4 1.4-1.1 2.8-2 4zm2.3-6H9.7a14 14 0 0 1 0-4h4.6a14 14 0 0 1 0 4zm.2 5.6c.6-1.1 1.1-2.3 1.4-3.6h3a8 8 0 0 1-4.4 3.6zM16.3 14a16 16 0 0 0 0-4h3.4a8 8 0 0 1 0 4zM16 8c-.3-1.3-.8-2.5-1.4-3.6A8 8 0 0 1 18.9 8z"/></svg>
        www.vfwayroutes.com
      </li>
    </ul>
    <span class="divider"></span>
    <address class="address">2740 Harlow Creek Rd<br>Brookvale, GA 30412</address>
  </section>

</main>
</body>
</html>
```